Namibia currently imports 60% of its food. Harvest Crest Oruva is an initiative which will assist Namibia to become self sustainable in terms of food production. We aim to do this through the development of 3 agricultural production zones which will include farming zones, local farmer assistance, processing and distribution of the final products. Please see our project overview attached.

```html
<!DOCTYPE html>
<html lang="en">
<head>
<meta charset="utf-8">
<title>Harvest Crest Oruva</title>
<link href="https://fonts.googleapis.com/css2?family=Outfit:wght@300;400;500;600;700&display=swap" rel="stylesheet">
<style>
:root{
  --green:#0f6b3a;
  --green-dark:#1e5a2c;
  --tan:#c8a27f;
  --tan-soft:#c9a584;
  --beige:#f6f2ec;
  --bubble:#edf1ee;
  --ink:#1a1a1a;
  --muted:#3c3c3c;
  --white:#ffffff;
  --star:#f4a51c;
}
*{margin:0;padding:0;box-sizing:border-box}
html,body{width:1200px;height:3271px;overflow:hidden}
body{font-family:'Outfit',sans-serif;color:var(--ink);background:var(--white);position:relative}
.abs{position:absolute}
.photo{position:absolute;overflow:hidden}

/* header */
.site-header{position:absolute;left:0;top:0;width:1200px;height:70px;background:var(--white)}
.brand{position:absolute;left:141px;top:24px;font-size:25px;font-weight:500;color:var(--green);letter-spacing:.5px;display:flex;align-items:center;gap:10px}
.brand .dot{width:12px;height:12px;border-radius:50%;background:var(--green)}
.nav{position:absolute;left:492px;top:27px;display:flex;gap:36px;font-size:13px;font-weight:500}
.btn-contact{position:absolute;left:950px;top:16px;width:109px;height:39px;border-radius:20px;background:var(--tan);color:var(--white);font-size:14px;font-weight:500;display:flex;align-items:center;justify-content:center}

/* hero */
.hero{position:absolute;left:0;top:70px;width:1200px;height:486px;background:linear-gradient(90deg,#f3f1ea 0%,#eeeee3 50%,#e3e8d5 100%)}
.hero h1{position:absolute;left:141px;top:112px;font-size:40px;font-weight:400;line-height:51px;width:420px}
.hero h1 b{font-weight:700}
.hero p{position:absolute;left:141px;top:278px;width:340px;font-size:15px;line-height:25px;font-weight:500}
.btn-green{position:absolute;background:var(--green);color:var(--white);border-radius:20px;font-size:14px;font-weight:500;display:flex;align-items:center;justify-content:center;gap:8px}

/* sections */
.section-title{position:absolute;left:0;width:1200px;text-align:center;font-size:28px;font-weight:600;color:var(--green)}
.rule{position:absolute;left:569px;width:62px;height:2px;background:var(--tan)}

.about h2{position:absolute;left:613px;top:657px;font-size:28px;font-weight:600;color:var(--green)}
.about .about-rule{position:absolute;left:613px;top:697px;width:62px;height:2px;background:var(--tan)}
.about .copy{position:absolute;left:613px;top:724px;width:435px;font-size:11.5px;line-height:22.5px;color:var(--muted)}
.about .copy p{margin-bottom:14px}
.btn-tan{position:absolute;background:var(--tan);color:var(--white);border-radius:20px;font-size:14px;font-weight:500;display:flex;align-items:center;justify-content:center;gap:8px}

.projects-band{position:absolute;left:0;top:1120px;width:1200px;height:420px;background:var(--beige)}
.project-card{position:absolute;top:1250px;width:292px;height:172px;border-radius:12px;overflow:hidden}
.project-info{position:absolute;top:1380px;width:248px;height:119px;border-radius:10px;background:var(--tan-soft);color:var(--white);padding:16px 18px}
.project-info h3{font-size:15px;font-weight:500;margin-bottom:9px}
.project-info p{font-size:10px;line-height:18px;width:210px;opacity:.95}
.arrow-circle{position:absolute;right:8px;bottom:10px;width:30px;height:30px;border-radius:50%;background:var(--white);display:flex;align-items:center;justify-content:center}

.bubble{position:absolute;top:1734px;width:447px;height:193px;border-radius:26px;background:var(--bubble)}
.bubble p{position:absolute;left:35px;width:380px;font-size:13.5px;line-height:20.5px;color:var(--ink)}
.bubble .tail{position:absolute;top:191px;left:82px;width:0;height:0;border-left:15px solid transparent;border-right:15px solid transparent;border-top:24px solid var(--bubble)}
.quote-badge{position:absolute;top:1710px;width:50px;height:48px;border-radius:12px 12px 12px 12px;background:var(--green);display:flex;align-items:center;justify-content:center}
.avatar{position:absolute;top:1967px;width:77px;height:77px;border-radius:50%}
.reviewer{position:absolute;top:1985px}
.reviewer .stars{display:flex;gap:5px}
.reviewer .name{font-size:17px;font-weight:500;margin-top:4px}
.slider-arrow{position:absolute;top:1819px;width:35px;height:35px;border-radius:50%;display:flex;align-items:center;justify-content:center}

.stats{position:absolute;left:141px;top:2130px;width:917px;height:221px;border-radius:40px;overflow:hidden;background:radial-gradient(ellipse at 60% 40%,#3f8a3a 0%,#2d7432 45%,#1f5d28 100%)}
.stat{position:absolute;top:68px;color:var(--white)}
.stat .num{font-size:34px;font-weight:600;line-height:38px}
.stat .label{font-size:12.5px;line-height:20px;margin-top:14px;width:110px}

.news-card{position:absolute;top:2534px;width:292px}
.news-card .img{height:179px;border-radius:10px}
.news-card .date{margin-top:16px;font-size:12px;color:var(--green);font-weight:500}
.news-card h3{margin-top:14px;font-size:15.5px;font-weight:500;line-height:23px}
.news-card .more{margin-top:18px;font-size:12px;color:var(--green);font-weight:600;text-decoration:underline;display:flex;align-items:center;gap:6px}

.site-footer{position:absolute;left:0;top:2927px;width:1200px;height:344px;background:radial-gradient(ellipse at 45% 30%,#2f6d34 0%,#1e5a2c 55%,#184d24 100%);color:var(--white)}
.site-footer .brand-f{position:absolute;left:141px;top:80px;font-size:26px;font-weight:500;display:flex;align-items:center;gap:10px}
.site-footer .brand-f .dot{width:12px;height:12px;border-radius:50%;background:var(--white)}
.footer-col{position:absolute;top:62px}
.footer-col h4{font-size:15px;font-weight:500;margin-bottom:18px}
.footer-col li{list-style:none;font-size:12px;margin-bottom:12px}
.newsletter h4{position:absolute;left:141px;top:162px;font-size:16px;font-weight:500}
.newsletter .field{position:absolute;left:141px;top:186px;width:272px;height:42px;border-radius:8px;background:var(--white);color:#555;font-size:12px;padding:13px 17px}
.newsletter .send{position:absolute;right:6px;top:6px;width:40px;height:30px;border-radius:6px;background:var(--tan);display:flex;align-items:center;justify-content:center}
.contact-row{display:flex;gap:12px;font-size:12px;line-height:18px;margin-bottom:12px}
.footer-line{position:absolute;left:141px;top:287px;width:917px;height:1px;background:rgba(255,255,255,.3)}
.copyright{position:absolute;left:141px;top:307px;font-size:12px}
.socials{position:absolute;left:926px;top:303px;display:flex;gap:11px}
.socials span{width:25px;height:25px;border-radius:50%;border:2px solid var(--white)}
</style>
</head>
<body>

<header class="site-header">
  <div class="brand"><span class="dot"></span>Harvest Crest Oruva</div>
  <nav class="nav"><span>About Us</span><span>Our Projects</span><span>Farmer Resources</span><span>News &amp; Updates</span></nav>
  <div class="btn-contact">Contact Us</div>
</header>

<section class="hero">
  <h1>Empowering Namibia To <b>Achieve Food Independence.</b></h1>
  <p>Reducing imports by fostering local agricultural production.</p>
  <div class="btn-green" style="left:141px;top:350px;width:196px;height:39px">Learn About Projects
    <svg width="18" height="10" viewBox="0 0 18 10"><path d="M1 5h15M12 1l4 4-4 4" stroke="#fff" stroke-width="1.5" fill="none"/></svg></div>
</section>
<div class="photo" role="img" aria-label="Woman in red headscarf tending leafy crops" style="left:615px;top:112px;width:214px;height:236px;border-radius:18px 0 0 0;background:linear-gradient(160deg,#8a6d3c,#5f7f2a 55%,#9bbb3c)"></div>
<div class="photo" role="img" aria-label="Farmer smiling beside a yellow tractor" style="left:615px;top:363px;width:214px;height:123px;border-radius:0 0 0 18px;background:linear-gradient(150deg,#5c5a2a,#b09a35 50%,#6c8a3a)"></div>
<div class="photo" role="img" aria-label="Woman in cap inspecting tall plants" style="left:845px;top:142px;width:213px;height:123px;border-radius:18px 18px 0 0;background:linear-gradient(150deg,#6f7f4a,#3e5a2a 60%,#8a8d5a)"></div>
<div class="photo" role="img" aria-label="Red tractor working rows of crops at sunset" style="left:845px;top:281px;width:213px;height:235px;border-radius:0 0 18px 0;background:linear-gradient(180deg,#6f8fb5 0%,#d2b88a 32%,#6d8a35 50%,#2f5a20 100%)"></div>

<section class="about">
  <div class="photo" role="img" aria-label="Farmer standing in a field at golden sunrise" style="left:141px;top:643px;width:148px;height:186px;border-radius:12px 0 0 0;background:linear-gradient(180deg,#f1d27a,#b98a2c 55%,#4c3a18)"></div>
  <div class="photo" role="img" aria-label="Rolling farmland hills in warm evening light" style="left:304px;top:643px;width:213px;height:186px;border-radius:0 12px 0 0;background:linear-gradient(180deg,#c9a868,#a6853a 50%,#6b5a28)"></div>
  <div class="photo" role="img" aria-label="Worker among large leafy crop rows" style="left:141px;top:843px;width:213px;height:192px;border-radius:0 0 0 12px;background:linear-gradient(180deg,#6d6a2a,#8e9a32 50%,#3d5a1c)"></div>
  <div class="photo" role="img" aria-label="Close view of broad green crop leaves" style="left:368px;top:843px;width:149px;height:192px;border-radius:0 0 12px 0;background:linear-gradient(180deg,#8a8a3a,#a8a23a 45%,#3a5a1e)"></div>
  <h2>About Us</h2>
  <div class="about-rule"></div>
  <div class="copy">
    <p>Namibia is a young democracy in Sub-Saharan Africa with a population of approximately 2.5 Million people. The country’s agricultural sector has been slow to keep up with the increasing population. As a consequence, approximately 60% of the food required to feed the nation is imported. The elevated cost of these imported foods means a large proportion of the population consume food with low nutritional value.</p>
    <p>Despite vast tracts of available arable land and abundant water resources (both above and below ground), the agricultural sector has struggled to capitalise. This is largely due to a lack of investment, technical knowledge and available technologies.</p>
  </div>
  <div class="btn-tan" style="left:613px;top:987px;width:136px;height:39px">Learn More
    <svg width="18" height="10" viewBox="0 0 18 10"><path d="M1 5h15M12 1l4 4-4 4" stroke="#fff" stroke-width="1.5" fill="none"/></svg></div>
</section>

<section class="projects">
  <div class="projects-band"></div>
  <div class="section-title" style="top:1167px">Our Projects</div>
  <div class="rule" style="top:1209px"></div>

  <div class="project-card" role="img" aria-label="Farmer carrying produce crate across green fields" style="left:141px;background:linear-gradient(180deg,#8a8a4a,#4f7a2c 45%,#3c5f22)"></div>
  <div class="project-info" style="left:163px"><h3>Farming Zones</h3><p>The country’s agricultural sector has been slow to keep up with the increasing population.</p>
    <div class="arrow-circle"><svg width="12" height="12" viewBox="0 0 12 12"><path d="M2 10L10 2M4 2h6v6" stroke="#c9a584" stroke-width="1.4" fill="none"/></svg></div></div>

  <div class="project-card" role="img" aria-label="Local farmers planting seedlings in soil" style="left:455px;background:linear-gradient(180deg,#4f7a3a,#9a6a3a 55%,#7a4a2a)"></div>
  <div class="project-info" style="left:477px"><h3>Local Farmer Assistance</h3><p>Despite vast tracts of available arable land and abundant water resources (both above and below ground)</p>
    <div class="arrow-circle"><svg width="12" height="12" viewBox="0 0 12 12"><path d="M2 10L10 2M4 2h6v6" stroke="#c9a584" stroke-width="1.4" fill="none"/></svg></div></div>

  <div class="project-card" role="img" aria-label="Workers in a greenhouse processing crops" style="left:770px;background:linear-gradient(180deg,#d8dcd8,#9aa69a 45%,#4a6a44)"></div>
  <div class="project-info" style="left:791px"><h3>Processing and Distribution</h3><p>Each of the allocated production zones will be furnished with handling, processing and milling facilities for all crops</p>
    <div class="arrow-circle"><svg width="12" height="12" viewBox="0 0 12 12"><path d="M2 10L10 2M4 2h6v6" stroke="#c9a584" stroke-width="1.4" fill="none"/></svg></div></div>
</section>

<section class="customers">
  <div class="section-title" style="top:1629px">Our Happy Customers</div>
  <div class="rule" style="top:1671px"></div>

  <div class="slider-arrow" style="left:118px;border:1.5px solid var(--green)"><svg width="10" height="14" viewBox="0 0 10 14"><path d="M7 2L2 7l5 5" stroke="#0f6b3a" stroke-width="1.8" fill="none"/></svg></div>
  <div class="slider-arrow" style="left:1038px;background:var(--green)"><svg width="10" height="14" viewBox="0 0 10 14"><path d="M3 2l5 5-5 5" stroke="#fff" stroke-width="1.8" fill="none"/></svg></div>

  <div class="bubble" style="left:136px"><p style="top:52px">A technically excellent Pilates training! Each training session includes new exercise sequences with precise instructions, and different small equipment is often used. My summary, definitely try it out, highly recommended. Thanks Ndapewa!</p><div class="tail"></div></div>
  <div class="quote-badge" style="left:192px"><svg width="24" height="20" viewBox="0 0 24 20"><path d="M2 2h8v8l-4 8H3l3-8H2zM14 2h8v8l-4 8h-3l3-8h-4z" fill="#fff"/></svg></div>
  <div class="avatar" role="img" aria-label="Portrait of reviewer" style="left:198px;background:linear-gradient(160deg,#b89a78,#6a5a44)"></div>
  <div class="reviewer" style="left:290px">
    <div class="stars">
      <svg width="16" height="16" viewBox="0 0 24 24"><path d="M12 2l3 7h7l-5.5 4.5 2 7.5L12 17l-6.5 4 2-7.5L2 9h7z" fill="#f4a51c"/></svg>
      <svg width="16" height="16" viewBox="0 0 24 24"><path d="M12 2l3 7h7l-5.5 4.5 2 7.5L12 17l-6.5 4 2-7.5L2 9h7z" fill="#f4a51c"/></svg>
      <svg width="16" height="16" viewBox="0 0 24 24"><path d="M12 2l3 7h7l-5.5 4.5 2 7.5L12 17l-6.5 4 2-7.5L2 9h7z" fill="#f4a51c"/></svg>
      <svg width="16" height="16" viewBox="0 0 24 24"><path d="M12 2l3 7h7l-5.5 4.5 2 7.5L12 17l-6.5 4 2-7.5L2 9h7z" fill="#f4a51c"/></svg>
      <svg width="16" height="16" viewBox="0 0 24 24"><path d="M12 2l3 7h7l-5.5 4.5 2 7.5L12 17l-6.5 4 2-7.5L2 9h7z" fill="#f4a51c"/></svg>
    </div>
    <div class="name">Tobias Hamutenya</div>
  </div>

  <div class="bubble" style="left:608px"><p style="top:49px">A technically excellent Pilates training! Each training session includes new exercise sequences with precise instructions, and different small equipment is often used. My summary, definitely try it out, highly recommended. Thanks Ndapewa!</p><div class="tail"></div></div>
  <div class="quote-badge" style="left:665px"><svg width="24" height="20" viewBox="0 0 24 20"><path d="M2 2h8v8l-4 8H3l3-8H2zM14 2h8v8l-4 8h-3l3-8h-4z" fill="#fff"/></svg></div>
  <div class="avatar" role="img" aria-label="Portrait of reviewer" style="left:671px;background:linear-gradient(160deg,#d8d8d0,#5a4a3a)"></div>
  <div class="reviewer" style="left:763px">
    <div class="stars">
      <svg width="16" height="16" viewBox="0 0 24 24"><path d="M12 2l3 7h7l-5.5 4.5 2 7.5L12 17l-6.5 4 2-7.5L2 9h7z" fill="#f4a51c"/></svg>
      <svg width="16" height="16" viewBox="0 0 24 24"><path d="M12 2l3 7h7l-5.5 4.5 2 7.5L12 17l-6.5 4 2-7.5L2 9h7z" fill="#f4a51c"/></svg>
      <svg width="16" height="16" viewBox="0 0 24 24"><path d="M12 2l3 7h7l-5.5 4.5 2 7.5L12 17l-6.5 4 2-7.5L2 9h7z" fill="#f4a51c"/></svg>
      <svg width="16" height="16" viewBox="0 0 24 24"><path d="M12 2l3 7h7l-5.5 4.5 2 7.5L12 17l-6.5 4 2-7.5L2 9h7z" fill="#f4a51c"/></svg>
      <svg width="16" height="16" viewBox="0 0 24 24"><path d="M12 2l3 7h7l-5.5 4.5 2 7.5L12 17l-6.5 4 2-7.5L2 9h7z" fill="#f4a51c"/></svg>
    </div>
    <div class="name">Selma Nangolo</div>
  </div>
</section>

<section class="stats" role="img" aria-label="Farmers working in green crop field behind statistics">
  <div class="stat" style="left:95px"><div class="num">95%</div><div class="label">Hectares Of Land Cultivated</div></div>
  <div class="stat" style="left:298px"><div class="num">3000+</div><div class="label">Farmers Assisted</div></div>
  <div class="stat" style="left:502px"><div class="num">100+</div><div class="label">Farmers In The Farm</div></div>
  <div class="stat" style="left:705px"><div class="num">80%</div><div class="label">Reduction In Food Imports</div></div>
</section>

<section class="news">
  <div class="section-title" style="top:2441px">Latest News And Updates</div>
  <div class="rule" style="top:2482px"></div>

  <article class="news-card" style="left:141px">
    <div class="img" role="img" aria-label="Woman holding a crate of fresh vegetables in a greenhouse" style="background:linear-gradient(160deg,#d8d6cc,#8a8a6a 50%,#4a6a2e)"></div>
    <div class="date">October 6, 2023</div>
    <h3>Despite vast tracts of available arable land and abundant water resources</h3>
    <div class="more">Read More <svg width="16" height="10" viewBox="0 0 16 10"><path d="M1 5h13M10 1l4 4-4 4" stroke="#0f6b3a" stroke-width="1.4" fill="none"/></svg></div>
  </article>
  <article class="news-card" style="left:454px">
    <div class="img" role="img" aria-label="Wide crop field under a blue sky" style="background:linear-gradient(180deg,#3f8fd8 0%,#a9d0ea 35%,#5f8a2a 50%,#2f5a1c 100%)"></div>
    <div class="date">September 19, 2023</div>
    <h3>Harvest Crest Oruva” initiative to be a vector for an accelerated change</h3>
    <div class="more">Read More <svg width="16" height="10" viewBox="0 0 16 10"><path d="M1 5h13M10 1l4 4-4 4" stroke="#0f6b3a" stroke-width="1.4" fill="none"/></svg></div>
  </article>
  <article class="news-card" style="left:766px">
    <div class="img" role="img" aria-label="Woman planting seedlings inside a greenhouse" style="background:linear-gradient(180deg,#e6e4dc,#a89a86 55%,#6a5240)"></div>
    <div class="date">November 8, 2023</div>
    <h3>Harvest Crest Oruva program would be to establish 3 distinct food production</h3>
    <div class="more">Read More <svg width="16" height="10" viewBox="0 0 16 10"><path d="M1 5h13M10 1l4 4-4 4" stroke="#0f6b3a" stroke-width="1.4" fill="none"/></svg></div>
  </article>
</section>

<footer class="site-footer">
  <div class="brand-f"><span class="dot"></span>Harvest Crest Oruva</div>
  <div class="newsletter">
    <h4>Newsletter</h4>
    <div class="field">Enter your email
      <div class="send"><svg width="16" height="16" viewBox="0 0 16 16"><path d="M14 2L2 7l5 2 2 5z" fill="#fff"/></svg></div></div>
  </div>
  <div class="footer-col" style="left:512px"><h4>Quick Links</h4><ul><li>About Us</li><li>Our Projects</li><li>Farmer Resources</li><li>News &amp; Updates</li></ul></div>
  <div class="footer-col" style="left:685px"><h4>Resources</h4><ul><li>Privacy Policy</li><li>Terms Of Service</li></ul></div>
  <div class="footer-col" style="left:852px"><h4>Contact Info</h4>
    <div class="contact-row"><svg width="18" height="20" viewBox="0 0 18 20"><path d="M9 1a6 6 0 0 0-6 6c0 5 6 10 6 10s6-5 6-10a6 6 0 0 0-6-6z" stroke="#fff" stroke-width="1.5" fill="none"/><circle cx="9" cy="7" r="2" fill="#fff"/><path d="M2 19h14" stroke="#fff" stroke-width="1.5"/></svg><span>14 Veld Lane, Block 7,<br>Okahandja Rd 90210</span></div>
    <div class="contact-row"><svg width="18" height="14" viewBox="0 0 18 14"><rect x="1" y="1" width="16" height="12" rx="1" fill="#fff"/><path d="M1 2l8 6 8-6" stroke="#1e5a2c" stroke-width="1.3" fill="none"/></svg><span>info@harvestcrestoruva.com</span></div>
    <div class="contact-row"><svg width="16" height="16" viewBox="0 0 16 16"><path d="M3 1l3 3-2 2c1 2 3 4 5 5l2-2 3 3-2 3C7 15 1 9 1 3z" fill="#fff"/></svg><span>555-014-2290</span></div>
  </div>
  <div class="footer-line"></div>
  <div class="copyright">© 2024 Harvest Crest Oruva. All rights reserved.</div>
  <div class="socials"><span></span><span></span><span></span><span></span></div>
</footer>

</body>
</html>
```